VELORA SPORTS NETWORK

design a website that will be a companion to a sports network that features womens sports and fitness content.
With the goal of promoting and empowering female athleticism, Velorabx.example will be the online network that connects female sports fans to the sports they love and follow. The site aims to raise the level of awareness of women in sports by providing comprehensive sports coverage, spotlighting outstanding achievements, and working with sporting associations on advocacy issues and empowering programs.
Updates
I would like to have all entry by Sunday June 8 2014 thank you
please use actual script not lorem ipsum
thank you
Deadline winding down, added new pictures to file
Target Market(s)
our target market is females 18-54, whom love womens sports and ftiness
Industry/Entity Type
Fitness
Font styles to use
Requirements
Must have
- Attributes of the website:
1. Large Photos: to accompany current stories
2. Colorful: Highlight Velora’s officials colors
3. News Area: recent news items on the home page and achieved news stories
4. Featured Content area: Headline news, athlete spotlights and issues
5. Streaming content: to accompany news and featured content
6. Advertiser links: to purchase merchandise
7. Real-time scores of live events
8. Blog
9. Monthly newsletter
10. Athlete profile page
11. Model close to KVRM
Nice to have
- Velorabx.example will offer value-added service that will entitle customers to gain access to online streaming services provided by Velora, which delivers both live streams and on-demand replays of global women’s sports events to sports fans in U.S. and abroad. This service will be subscription based for a modest monthly fee. Content will be available across multiple platforms and cloud based. New subscriber will get first 30 days free.
Content will include:
1. Live sports events
2. On-demand and premium content
3. Fan-generated Content

```html
<!DOCTYPE html>
<html lang="en">
<head>
<meta charset="utf-8">
<title>Velora Sports Network</title>
<link href="https://fonts.googleapis.com/css2?family=Oswald:wght@400;500&family=Open+Sans:ital,wght@0,400;0,600;0,700;1,400;1,700&display=swap" rel="stylesheet">
<style>
:root{
  --red:#de3431;
  --red-dark:#a8201e;
  --navy:#252c36;
  --navy-line:#3b4450;
  --orange:#f26a2e;
  --ink:#1b1b1b;
  --grey:#6b6b6b;
  --white:#ffffff;
  --fb:#3b5fa8;
  --tw:#2aa3dd;
  --gp:#d2483b;
}
*{box-sizing:border-box;margin:0;padding:0}
html,body{width:1200px;height:2639px;overflow:hidden;background:var(--white)}
body{font-family:"Open Sans",Arial,sans-serif;color:var(--ink);position:relative}
.display{font-family:"Oswald",Arial,sans-serif;text-transform:uppercase;font-weight:500}
.accent{color:var(--red)}
.abs{position:absolute}
.photo{position:absolute}

/* header */
.site-header{position:absolute;left:0;top:0;width:1200px;height:158px;background:var(--navy)}
.brand{position:absolute;left:120px;top:16px;display:flex;flex-direction:column;align-items:flex-start;gap:8px}
.brand-mark{width:62px;height:62px;border-radius:50%;background:var(--red)}
.brand-name{font-family:"Oswald",sans-serif;font-weight:500;color:var(--red);font-size:14px;letter-spacing:1px;line-height:1.15;width:120px}
.quick-form{position:absolute;right:110px;top:48px;display:flex;gap:10px}
.quick-form .field{width:168px;height:36px;border:1px solid #4d5662;color:#7c8590;font-size:12px;padding:10px}
.btn-red{background:var(--red);color:var(--white);font-family:"Oswald",sans-serif;font-size:12px;text-transform:uppercase;display:flex;align-items:center;justify-content:center;height:36px;padding:0 12px}
.main-nav{position:absolute;right:110px;top:118px;display:flex;gap:22px;font-family:"Oswald",sans-serif;font-size:18px;text-transform:uppercase;color:var(--white)}
.main-nav .current{color:var(--orange)}

/* hero */
.hero{position:absolute;left:0;top:158px;width:1200px;height:493px;overflow:hidden;
  background:
    radial-gradient(ellipse 180px 260px at 640px 250px,#c9ccd0 0%,#8d9298 40%,rgba(60,64,70,0) 100%),
    radial-gradient(ellipse at 55% 55%,#6a7078 0%,#2b2f35 45%,#050506 80%)}
.hero-ground{position:absolute;left:360px;top:330px;width:760px;height:163px;background:linear-gradient(180deg,rgba(120,124,130,.5),rgba(20,22,26,.9))}
.news-panel{position:absolute;left:110px;top:220px;width:310px;height:273px;background:var(--white)}
.news-head{height:52px;background:var(--red);color:var(--white);display:flex;align-items:center;padding:0 14px;font-family:"Oswald",sans-serif;font-size:15px;text-transform:uppercase}
.news-head .arrows{margin-left:auto;display:flex;gap:18px;font-size:18px}
.news-item{padding:8px 8px 9px;border-bottom:1px solid #e6e6e6}
.news-date{font-size:12px;color:#a5a5a5;font-style:italic}
.news-title{font-size:12px;color:var(--red);margin-top:4px;font-weight:600}
.news-text{font-size:11px;line-height:1.4;margin-top:6px}
.news-more{font-size:11px;color:var(--grey);margin-top:4px}
.hero-tab{position:absolute;top:442px;height:51px;width:309px;background:var(--red);color:var(--white);font-family:"Oswald",sans-serif;font-size:15px;text-transform:uppercase;display:flex;align-items:center;padding-left:14px;gap:10px}

/* welcome */
.welcome-title{position:absolute;top:696px;left:0;width:1200px;text-align:center;font-size:27px}
.welcome-lead{position:absolute;top:748px;left:110px;width:980px;text-align:center;font-size:14px;font-style:italic;font-weight:700}
.welcome-body{position:absolute;top:782px;left:130px;width:940px;text-align:center;font-size:12px;color:var(--grey);line-height:1.45}
.offer{position:absolute;top:846px;width:210px}
.offer h3{font-size:15px;line-height:1.45;height:52px}
.offer .thumb{width:210px;height:125px}
.offer h4{font-family:"Oswald",sans-serif;font-weight:400;font-size:13px;margin-top:16px}
.offer p{font-size:10.5px;font-style:italic;color:var(--grey);line-height:1.45;margin-top:10px;width:170px}
.circle-arrow{position:absolute;width:18px;height:18px;border:1px solid #c9c9c9;border-radius:50%;color:#aaa;font-size:11px;line-height:1;display:flex;align-items:center;justify-content:center;top:838px}

/* stories */
.stories{position:absolute;left:0;top:1142px;width:1200px;height:453px;background:var(--red);color:var(--white)}
.stories-title{position:absolute;left:588px;top:40px;font-size:27px;color:var(--white)}
.stories-title .dark{color:var(--navy)}
.stories-lead{position:absolute;left:588px;top:88px;width:455px;font-size:12px;font-style:italic;font-weight:700;line-height:1.45;color:#2a0a0a}
.stories-copy{position:absolute;left:588px;top:130px;width:455px;font-size:11.5px;line-height:1.45;color:#fde6e4}
.stories-copy p+p{margin-top:8px}
.btn-dark{position:absolute;left:588px;top:282px;width:96px;height:52px;background:var(--red-dark);font-size:12px;display:flex;align-items:center;justify-content:center}

/* newsletter */
.newsletter{position:absolute;left:0;top:1595px;width:1200px;height:176px;background:var(--navy)}
.newsletter h2{position:absolute;left:110px;top:30px;font-size:16px;color:var(--white)}
.newsletter .sub{position:absolute;left:110px;top:56px;font-size:10.5px;font-style:italic;color:#6d7682}
.newsletter .form{position:absolute;left:110px;top:87px;display:flex;gap:4px}
.newsletter .field{width:226px;height:62px;border:1px solid var(--navy-line);color:#7c8590;font-size:13px;padding:22px 12px}
.newsletter .btn-red{height:62px;width:98px;font-size:15px}
.ad-cta{position:absolute;left:128px;top:44px;width:82px;height:26px;background:var(--red);color:#fff;font-size:12px;display:flex;align-items:center;justify-content:center}
.ad-title{position:absolute;left:0;top:84px;width:335px;text-align:center;font-family:"Oswald",sans-serif;font-size:26px;color:#fff;letter-spacing:2px;text-transform:uppercase}
.ad-url{position:absolute;left:0;top:122px;width:335px;text-align:center;font-size:8px;color:#c8ccd2}

/* blog */
.blog-title{position:absolute;top:1792px;left:0;width:1200px;text-align:center;font-size:27px}
.blog-lead{position:absolute;top:1838px;left:0;width:1200px;text-align:center;font-size:14px;font-style:italic;font-weight:700}
.post{position:absolute;text-align:center}
.post h3{font-size:15px;font-weight:400}
.post time{display:block;color:var(--red);font-size:11px;margin-top:8px}
.post p{font-size:13px;line-height:1.55;margin-top:10px}
.shares{display:flex;justify-content:center;gap:10px;margin-top:16px}
.share{width:40px;height:40px;border:2px solid}
.share.a{border-color:var(--fb)}
.share.b{border-color:var(--tw)}
.share.c{border-color:var(--gp)}

/* footer */
.site-footer{position:absolute;left:0;top:2400px;width:1200px;height:239px;background:var(--navy);text-align:center}
.site-footer h2{position:absolute;top:20px;width:1200px;font-size:24px;color:#5a6370}
.socials{position:absolute;top:70px;left:0;width:1200px;display:flex;justify-content:center;gap:18px}
.socials span{width:44px;height:44px;border:1px solid #4a535f;border-radius:50%}
.footer-nav{position:absolute;top:150px;width:1200px;display:flex;justify-content:center;gap:26px;font-family:"Oswald",sans-serif;font-size:18px;text-transform:uppercase;color:var(--white)}
.footer-nav .current{color:var(--orange)}
.copyright{position:absolute;top:202px;width:1200px;font-size:11px;color:#7c8590}
</style>
</head>
<body>

<header class="site-header">
  <div class="brand">
    <span class="brand-mark"></span>
    <span class="brand-name">VELORA SPORTS NETWORK</span>
  </div>
  <div class="quick-form">
    <span class="field">Enter your Name</span>
    <span class="field">Enter your Mail id</span>
    <span class="btn-red">Register</span>
    <span class="btn-red" style="margin-left:-6px">Login</span>
  </div>
  <nav class="main-nav">
    <span class="current">Sports</span><span>Events</span><span>Complex</span><span>Social</span>
  </nav>
</header>

<section class="hero">
  <div class="hero-ground" role="img" aria-label="Athlete striking a ball in a floodlit stadium"></div>
  <div class="news-panel">
    <div class="news-head">+&nbsp;&nbsp;Latest News<span class="arrows">&lsaquo;<span>&rsaquo;</span></span></div>
    <div class="news-item">
      <div class="news-date">March 14 2014</div>
      <div class="news-title">League Final Is Set</div>
      <div class="news-text">Both semifinals went to extra time, setting up a rematch of last season’s title game.</div>
      <div class="news-more">Read More...</div>
    </div>
    <div class="news-item" style="border:0">
      <div class="news-date">March 14 2014</div>
      <div class="news-title">Record Crowd in Denver</div>
      <div class="news-text">Over 20,000 fans watched the opener live</div>
      <div class="news-more">Read More...</div>
    </div>
  </div>
  <div class="hero-tab" style="left:446px">+ <span>Upcoming Events</span></div>
  <div class="hero-tab" style="left:780px">+ <span>Live Event Score</span></div>
</section>

<h2 class="welcome-title display">Welcome to <span class="accent">VeloraTV</span></h2>
<p class="welcome-lead">Velorabx.example will offer value-added service that will entitle customers to gain access to online streaming services provided by Velora,</p>
<p class="welcome-body">which delivers both live streams and on-demand replays of global women’s sports events to sports fans in U.S. and abroad. This service will be subscription based for a modest monthly fee. Content will be available across multiple platforms and cloud based. New subscriber will get first 30 days free.</p>

<article class="offer" style="left:102px">
  <h3 class="display">Live Sports <span class="accent">Events</span></h3>
  <div class="thumb" role="img" aria-label="Lacrosse players on a green field" style="background:linear-gradient(180deg,#8a8f86,#d8d8d8 35%,#6f9a55 70%,#4e7a3e)"></div>
  <h4>The Forgotten Finals of ’94</h4>
  <p>Coming Tuesday: Marlow is now in it to coach, but Harbor Hawks haven’t called</p>
</article>
<article class="offer" style="left:313px">
  <h3 class="display">On-Demand and <span class="accent">Premium Content</span></h3>
  <div class="thumb" role="img" aria-label="American football players tackling" style="background:linear-gradient(180deg,#2a2f2a,#7a2a24 45%,#c7a84a 70%,#3d4a34)"></div>
  <h4>The Forgotten Finals of ’94</h4>
  <p>Coming Tuesday: Marlow is now in it to coach, but Harbor Hawks haven’t called</p>
</article>
<article class="offer" style="left:525px">
  <h3 class="display">Fan-Generated <span class="accent">Content</span></h3>
  <div class="thumb" role="img" aria-label="Football match action on a pitch" style="background:linear-gradient(180deg,#1e2430,#6a7a98 40%,#3a6a2e 75%,#2e5e2a)"></div>
  <h4>The Forgotten Finals of ’94</h4>
  <p>Coming Tuesday: Marlow is now in it to coach, but Harbor Hawks haven’t called</p>
</article>
<span class="circle-arrow" style="left:1044px">&lsaquo;</span>
<span class="circle-arrow" style="left:1070px">&rsaquo;</span>
<div class="photo" role="img" aria-label="Team photo of a football squad with a play button" style="left:787px;top:866px;width:303px;height:237px;background:linear-gradient(180deg,#1e2a20 0%,#8a1f1f 30%,#b52424 55%,#d8d8d8 78%,#2f5a2a 100%)">
  <svg class="abs" style="left:128px;top:95px" width="46" height="46" viewBox="0 0 46 46"><circle cx="23" cy="23" r="22" fill="#f26a2e"/><path d="M18 13 L33 23 L18 33 Z" fill="#fff"/></svg>
</div>

<section class="stories">
  <div class="photo" role="img" aria-label="Footballer celebrating on his knees" style="left:110px;top:45px;width:445px;height:301px;background:linear-gradient(180deg,#3a4540 0%,#5c6a58 30%,#4f8a3a 60%,#3f7a32 100%)"></div>
  <div class="photo" role="img" aria-label="Ice hockey player" style="left:110px;top:346px;width:111px;height:85px;background:linear-gradient(180deg,#d9dde4,#1d2c5a)"></div>
  <div class="photo" role="img" aria-label="American football player" style="left:221px;top:346px;width:111px;height:85px;background:linear-gradient(180deg,#2e6a36,#d4a429)"></div>
  <div class="photo" role="img" aria-label="Footballer portrait" style="left:332px;top:346px;width:111px;height:85px;background:linear-gradient(180deg,#2b3d2a,#b88a70)"></div>
  <div class="photo" role="img" aria-label="Hockey players on ice" style="left:443px;top:346px;width:112px;height:85px;background:linear-gradient(180deg,#f0f0f0,#c04040)"></div>
  <h2 class="stories-title display"><span class="dark">Current</span> Stories</h2>
  <p class="stories-lead">Each week we spotlight the athletes, teams and moments that are shaping the future of women’s sport...</p>
  <div class="stories-copy">
    <p>From record crowds at the league opener to a first-ever sellout in the college semifinals, women’s sport is drawing more fans than ever. Our writers cover the games, the rivalries and the people who make them matter.</p>
    <p>This month we follow three rising stars through a season of early mornings, long road trips and big wins, and talk with the coaches and associations working to grow youth programs and equal access to training across the country.</p>
  </div>
  <span class="btn-dark">View Details</span>
</section>

<section class="newsletter">
  <h2 class="display">Subscribe our <span class="accent">News Letter</span></h2>
  <p class="sub">Get our monthly roundup of live scores, athlete spotlights and new streams sent right to your inbox every month.</p>
  <div class="form">
    <span class="field">Enter Your Name</span>
    <span class="field">Enter Your Mail ID</span>
    <span class="btn-red">Subscribe</span>
  </div>
  <div class="photo" role="img" aria-label="Advertisement for a position camp with players" style="left:755px;top:15px;width:335px;height:142px;background:linear-gradient(180deg,#5a5f66,#1a1c20)">
    <span class="ad-cta">Join Now</span>
    <span class="ad-title">Position Camp</span>
    <span class="ad-url">FIELDLINE.EXAMPLE</span>
  </div>
</section>

<h2 class="blog-title display">Recent <span class="accent">Blog Post</span></h2>
<p class="blog-lead">Stories, opinions and training notes from our community</p>

<div class="photo" role="img" aria-label="Hockey players facing off in an arena" style="left:110px;top:1912px;width:478px;height:203px;background:linear-gradient(90deg,#8a1e1e 0%,#b03028 30%,#4a5a70 60%,#1c1c1c 100%)"></div>
<article class="post" style="left:110px;top:2136px;width:478px">
  <h3>Post With Large Image</h3>
  <time>May8, 2014</time>
  <p>What it takes to play through a full hockey season: our captain shares her routine for recovery, travel and staying sharp.</p>
  <div class="shares"><span class="share a"></span><span class="share b"></span><span class="share c"></span></div>
</article>

<div class="photo" role="img" aria-label="Sprinters racing on a running track" style="left:612px;top:1912px;width:215px;height:203px;background:linear-gradient(180deg,#9ab8d6 0%,#c9b8a8 40%,#b0522e 70%,#8a3a22 100%)"></div>
<article class="post" style="left:842px;top:1912px;width:250px">
  <h3>Post With Large Image</h3>
  <time>May8, 2014</time>
  <p>Five sprint drills our track coaches use to build a faster start, with tips for every level of runner.</p>
  <div class="shares"><span class="share a"></span><span class="share b"></span><span class="share c"></span></div>
</article>

<div class="photo" role="img" aria-label="Footballer kicking a ball on grass" style="left:612px;top:2135px;width:215px;height:205px;background:linear-gradient(180deg,#d8d4cc 0%,#3a4a8a 40%,#5a9a42 75%,#4f8a3a 100%)"></div>
<article class="post" style="left:842px;top:2135px;width:250px">
  <h3>Post With Large Image</h3>
  <time>May8, 2014</time>
  <p>Inside the youth football clinic that brought 300 girls onto the pitch for a weekend of games and coaching.</p>
  <div class="shares"><span class="share a"></span><span class="share b"></span><span class="share c"></span></div>
</article>

<footer class="site-footer">
  <h2 class="display">Follow Us</h2>
  <div class="socials" aria-label="Social links">
    <span></span><span></span><span></span><span></span><span></span>
  </div>
  <nav class="footer-nav"><span class="current">Sports</span><span>Events</span><span>Complex</span><span>Social</span></nav>
  <p class="copyright">Copyright © 2014</p>
</footer>

</body>
</html>
```